SkyvornQ Business Cards and Stationary Design

Need a design for our business cards and stationary. I want to carry on the theme of the logo. I want the business cards to have a design on the back. I would like the business cards and the stationary to carry the same theme, design scheme, and branding

Target Market(s)

Airlines and Maintenance Facilities

Industry/Entity Type

Aviation

Contact Information for Business Card

Name
Position Title
Address: 4827 Trellis Hollow Road, Brindlemoor, Calvera, 34951
Office Number
Mobile Number
Email
Website

Font styles to use
Serif
Sans Serif

Colors

Designer to choose colors to be used in the design.

```html
<!DOCTYPE html>
<html lang="en">
<head>
<meta charset="utf-8">
<title>SkyvornQ Business Card</title>
<link href="https://fonts.googleapis.com/css2?family=Work+Sans:wght@400;500;700&display=swap" rel="stylesheet">
<style>
  :root {
    --page-bg: #e9e9e9;
    --brand-blue: #27a4dd;
    --navy: #15264d;
    --text-grey: #4a4f5c;
    --divider: #3c4660;
    --white: #ffffff;
  }
  html, body {
    margin: 0;
    padding: 0;
    width: 1200px;
    height: 960px;
    overflow: hidden;
    background: var(--page-bg);
    font-family: "Work Sans", Arial, sans-serif;
  }
  .canvas {
    position: relative;
    width: 1200px;
    height: 960px;
  }
  .card {
    position: absolute;
    left: 270px;
    width: 664px;
    height: 380px;
    box-shadow: 0 4px 10px rgba(0,0,0,0.25);
  }
  .card-front {
    top: 72px;
    background: var(--brand-blue);
    color: var(--white);
  }
  .card-back {
    top: 509px;
    background: var(--white);
  }
  .front-mark {
    position: absolute;
    left: 277px;
    top: 80px;
    width: 110px;
    height: 110px;
    border-radius: 50%;
    background: var(--white);
  }
  .front-name {
    position: absolute;
    left: 0;
    right: 0;
    top: 226px;
    text-align: center;
    font-size: 48px;
    font-weight: 700;
    letter-spacing: 9px;
    text-indent: 9px;
    line-height: 1;
  }
  .front-url {
    position: absolute;
    left: 0;
    right: 0;
    top: 315px;
    text-align: center;
    font-size: 16px;
    font-weight: 700;
  }
  .back-mark {
    position: absolute;
    left: 155px;
    top: 104px;
    width: 92px;
    height: 92px;
    border-radius: 50%;
    background: var(--navy);
  }
  .back-name {
    position: absolute;
    left: 51px;
    width: 300px;
    top: 202px;
    text-align: center;
    font-size: 31px;
    font-weight: 700;
    letter-spacing: 6px;
    text-indent: 6px;
    color: var(--navy);
    line-height: 1;
  }
  .divider {
    position: absolute;
    left: 369px;
    top: 98px;
    width: 1.5px;
    height: 155px;
    background: var(--divider);
  }
  .contact {
    position: absolute;
    left: 407px;
    top: 96px;
  }
  .person-name {
    font-size: 24px;
    font-weight: 500;
    letter-spacing: 1px;
    color: var(--navy);
    line-height: 1;
  }
  .person-title {
    margin-top: 4px;
    font-size: 15px;
    color: var(--text-grey);
  }
  .contact-list {
    list-style: none;
    margin: 32px 0 0;
    padding: 0;
  }
  .contact-list li {
    display: flex;
    align-items: center;
    height: 20px;
    font-size: 15px;
    color: var(--text-grey);
    letter-spacing: 0.3px;
  }
  .contact-list svg {
    width: 11px;
    height: 11px;
    margin-right: 10px;
    fill: none;
    stroke: var(--navy);
    stroke-width: 1.6;
  }
  .address {
    position: absolute;
    left: 0;
    right: 0;
    top: 333px;
    text-align: center;
    font-size: 15px;
    color: var(--navy);
    letter-spacing: 0.3px;
  }
</style>
</head>
<body>
<main class="canvas">
  <section class="card card-front">
    <div class="front-mark"></div>
    <div class="front-name">SKYVORNQ</div>
    <div class="front-url">www.skyvornq.com</div>
  </section>

  <section class="card card-back">
    <div class="back-mark"></div>
    <div class="back-name">SKYVORNQ</div>
    <div class="divider"></div>
    <div class="contact">
      <div class="person-name">MARLEN COSTA</div>
      <div class="person-title">CEO/Founder</div>
      <ul class="contact-list">
        <li><svg viewBox="0 0 12 12"><rect x="3" y="1" width="6" height="10" rx="1"/><line x1="5.5" y1="9" x2="6.5" y2="9"/></svg>555-214-0967</li>
        <li><svg viewBox="0 0 12 12"><path d="M2 1.5l2 0 1 3-1.3 1a6 6 0 0 0 2.8 2.8l1-1.3 3 1v2a1 1 0 0 1-1 1A9 9 0 0 1 1 2.5a1 1 0 0 1 1-1z"/></svg>555-214-0967</li>
        <li><svg viewBox="0 0 12 12"><rect x="1" y="2.5" width="10" height="7"/><polyline points="1,2.5 6,6.5 11,2.5"/></svg>www.skyvornqmail.com</li>
        <li><svg viewBox="0 0 12 12"><circle cx="6" cy="6" r="5"/><ellipse cx="6" cy="6" rx="2.2" ry="5"/><line x1="1" y1="6" x2="11" y2="6"/></svg>www.skyvornq.com</li>
      </ul>
    </div>
    <div class="address">4827 Trellis Hollow Road, Brindlemoor, Calvera, 34951</div>
  </section>
</main>
</body>
</html>
```